Tolvik Commercial Cleaning is lookong for a new business card design.

A fresh new design that's professional and stylish. We need a serious upgrade to our business cards. I have included pictures of our existing ones. Our clients include professional individuals and business owners. We woupdblike something professional and upbeat. Please have fun and see what you come uo with.

Target Market(s)

Property managers, business owners, facility managers and other similar professionals

Industry/Entity Type

Janitorial

Contact Information for Business Card

Name, cell, office number, email, web address

Font styles to use
Sans Serif

Colors

Designer to choose colors to be used in the design.

Requirements
Must have
• please use the green color in our logo
Nice to have
• Bar code
Should not have
• Address

```html
<!DOCTYPE html>
<html lang="en">
<head>
<meta charset="utf-8">
<title>Tolvik Commercial Cleaning – Business Card</title>
<link rel="stylesheet" href="https://fonts.googleapis.com/css2?family=Open+Sans:wght@400;600;700;800&display=swap">
<style>
  :root {
    --page-bg: #e9e7e3;
    --card-bg: #1f2023;
    --card-deep: #151618;
    --brand-green: #3cb55a;
    --brand-blue: #3f79c0;
    --text-light: #f2f2f2;
    --ghost: #121315;
    --silver: #bfc1c4;
  }
  * { box-sizing: border-box; margin: 0; padding: 0; }
  html, body {
    width: 1200px; height: 780px; overflow: hidden;
    background: var(--page-bg);
    font-family: "Open Sans", Arial, sans-serif;
  }
  .canvas {
    width: 1200px; height: 780px;
    display: flex; align-items: center; justify-content: center; gap: 40px;
  }
  .card {
    position: relative;
    width: 560px; height: 320px;
    border-radius: 22px;
    background: var(--card-bg);
    overflow: hidden;
    box-shadow: 0 10px 28px rgba(0,0,0,.25);
  }

  /* Front */
  .front .brand-name {
    position: absolute; left: 150px; top: 28px;
    font-size: 82px; font-weight: 800; line-height: 1;
    color: var(--brand-green); letter-spacing: -1px;
  }
  .front .ghost-name {
    position: absolute; right: -40px; bottom: -34px;
    font-size: 150px; font-weight: 800; line-height: 1;
    color: var(--ghost); letter-spacing: -3px;
  }
  .front .contact {
    position: absolute; left: 26px; bottom: 30px;
    list-style: none; color: var(--text-light);
    font-size: 14px; line-height: 20px;
  }
  .front .contact li { display: flex; align-items: center; gap: 8px; }
  .front .contact svg { width: 12px; height: 12px; fill: var(--brand-green); flex: none; }
  .front .person {
    position: absolute; right: 38px; top: 150px; text-align: right;
  }
  .front .person-name {
    font-size: 24px; font-weight: 700; line-height: 1.15;
  }
  .front .first { color: var(--brand-green); }
  .front .last { color: var(--brand-blue); }
  .front .person-role {
    font-size: 17px; color: var(--text-light); margin-top: 2px;
  }
  .front .accent-bar {
    position: absolute; right: 0; top: 150px;
    width: 16px; height: 62px; background: var(--brand-green);
  }

  /* Back */
  .back .pattern-field {
    position: absolute; inset: 0;
    background: linear-gradient(215deg, var(--silver) 0%, #5d5f63 18%, var(--card-bg) 40%, var(--card-deep) 100%);
  }
  .back .brand-name {
    position: absolute; left: 300px; top: 196px;
    font-size: 34px; font-weight: 800; line-height: 1;
    color: var(--brand-green);
  }
</style>
</head>
<body>
<main class="canvas">
  <section class="card front" aria-label="Business card front">
    <div class="ghost-name" aria-hidden="true">Tolvik</div>
    <div class="brand-name">Tolvik</div>
    <div class="person">
      <div class="person-name"><span class="first">Marco</span> <span class="last">Delaney</span></div>
      <div class="person-role">Director</div>
    </div>
    <div class="accent-bar"></div>
    <ul class="contact">
      <li>
        <svg viewBox="0 0 24 24" aria-hidden="true"><path d="M6.6 10.8a15.1 15.1 0 0 0 6.6 6.6l2.2-2.2a1 1 0 0 1 1-.25 11.4 11.4 0 0 0 3.6.57 1 1 0 0 1 1 1V20a1 1 0 0 1-1 1A17 17 0 0 1 3 4a1 1 0 0 1 1-1h3.5a1 1 0 0 1 1 1c0 1.25.2 2.45.57 3.57a1 1 0 0 1-.25 1z"/></svg>
        (555) 014-2207
      </li>
      <li>
        <svg viewBox="0 0 24 24" aria-hidden="true"><path d="M3 5h18v14H3z M4 6l8 7 8-7" fill="none" stroke="#3cb55a" stroke-width="2.5"/></svg>
        marco@tolvikcleaning.com
      </li>
      <li>
        <svg viewBox="0 0 24 24" aria-hidden="true"><circle cx="12" cy="12" r="10"/></svg>
        www.tolvikcleaning.com
      </li>
    </ul>
  </section>

  <section class="card back" aria-label="Business card back">
    <div class="pattern-field" role="img" aria-label="Repeating brand name pattern on black with a silver sheen in the upper right corner"></div>
    <div class="brand-name">Tolvik</div>
  </section>
</main>
</body>
</html>
```